KRT Project Signage

Need a sign to be displayed in the front of properties currently under Construction or Renovation to advertise our company information. Need it to be Professional and Contemporary. We are a Design/Build Construction Company. Information should include Company Name, email, website, phone number. Attached: Logo and company brochure, also included and inspiration images

```html
<!DOCTYPE html>
<html lang="en">
<head>
<meta charset="utf-8">
<title>KRT Project Signage</title>
<link rel="stylesheet" href="https://fonts.googleapis.com/css2?family=Source+Sans+3:wght@600;700&display=swap">
<style>
  :root {
    --page-bg: #e9ecef;
    --sky-top: #0092f5;
    --sky-mid: #48b4f8;
    --sign-white: #ffffff;
    --ink-navy: #163f8c;
    --ink-black: #111111;
    --accent-yellow: #f2e83c;
    --art-deep: #1f4fb0;
    --art-mid: #5b8fe0;
    --art-light: #d6e9fb;
  }
  html, body {
    margin: 0;
    padding: 0;
    width: 1200px;
    height: 1200px;
    overflow: hidden;
    background: var(--page-bg);
  }
  .canvas {
    position: relative;
    width: 1200px;
    height: 1200px;
  }
  .sign {
    position: absolute;
    left: 167px;
    top: 30px;
    width: 866px;
    height: 1140px;
    overflow: hidden;
    background: linear-gradient(180deg,
      var(--sky-top) 0%,
      var(--sky-top) 20%,
      var(--sky-mid) 32%,
      var(--sign-white) 55%,
      var(--sign-white) 100%);
    box-shadow: 0 6px 24px rgba(0,0,0,0.18);
    font-family: "Source Sans 3", "Segoe UI", sans-serif;
  }
  .brand {
    position: absolute;
    top: 200px;
    left: 0;
    width: 100%;
    display: flex;
    justify-content: center;
    align-items: center;
    gap: 20px;
  }
  .brand-name {
    font-weight: 700;
    font-size: 62px;
    letter-spacing: 1px;
    color: var(--ink-black);
    line-height: 1;
  }
  .brand-mark {
    width: 46px;
    height: 46px;
    border-radius: 50%;
    background: var(--accent-yellow);
  }
  .house-art {
    position: absolute;
    left: 90px;
    top: 380px;
    width: 696px;
    height: 400px;
  }
  .contact {
    position: absolute;
    left: 0;
    width: 100%;
    text-align: center;
    color: var(--ink-navy);
    margin: 0;
    line-height: 1;
    font-weight: 700;
  }
  .contact-phone {
    top: 815px;
    font-size: 114px;
    letter-spacing: -1px;
  }
  .contact-email {
    top: 946px;
    font-size: 62px;
  }
  .contact-web {
    top: 1020px;
    font-size: 62px;
  }
</style>
</head>
<body>
<div class="canvas">
  <section class="sign">
    <div class="brand">
      <span class="brand-name">KRT CONSTRUCTION</span>
      <span class="brand-mark"></span>
    </div>

    <svg class="house-art" viewBox="0 0 696 400" role="img" aria-label="Blueprint-style illustration of a single-storey house with attached garage on a perspective grid">
      <defs>
        <linearGradient id="houseFill" x1="0" y1="0" x2="0" y2="1">
          <stop offset="0%" stop-color="var(--art-light)"/>
          <stop offset="45%" stop-color="var(--art-mid)"/>
          <stop offset="100%" stop-color="var(--art-deep)"/>
        </linearGradient>
      </defs>
      <rect x="0" y="0" width="696" height="400" rx="18" fill="url(#houseFill)"/>
    </svg>

    <p class="contact contact-phone">561-555-0148</p>
    <p class="contact contact-email">info@krtconstruction.com</p>
    <p class="contact contact-web">www.krtconstruction.com</p>
  </section>
</div>
</body>
</html>
```